Kestrelway Financial Plans

I am looking for a complete resdesign of my small financial presentation. This is a Word Doc/PDF that I print off when meeting with people in private. I often present my "two pager" that I have been using for years and years. It tells them the basics of what I do, how I help people and foundational financial principles.

I have recently gone out on my own in business and have completely rebranded. This presentation is my most used tool, so it is the first of many things I would like to redo. I am hoping it will somehow coordinate with the colors of my business, not necessarily the EXACT same 3 colors everywhere, but have the design colors compliment.

I've uploaded all my logo designs, as well as the current "two-pager". I am not against it going to 3 pages if needed. As it will still land on 2 pages with duplex printing.

It has always been VERY simple. I am wanting it built into a more professional and design specific format, to show off my branding, without being over cluttered.

I am completely open to ANY graphics changes. Obviously some are very novice, the house on the last page has always been overly simplified.

```html
<!DOCTYPE html>
<html lang="en">
<head>
<meta charset="utf-8">
<title>Kestrelway Financial Plans – Client Presentation</title>
<link rel="stylesheet" href="https://fonts.googleapis.com/css2?family=Bebas+Neue&family=Montserrat:wght@500;600;700;800&display=swap">
<style>
  :root{
    --navy:#16213a;
    --green:#1fae4b;
    --grey:#a6a8ab;
    --panel:#eeeeee;
    --backdrop:#e8e8e8;
    --white:#ffffff;
    --ink:#2b2f36;
    --head:'Bebas Neue', sans-serif;
    --body:'Montserrat', sans-serif;
  }
  *{box-sizing:border-box;margin:0;padding:0}
  html,body{width:1200px;height:605px;overflow:hidden;background:var(--backdrop);font-family:var(--body);color:var(--ink)}
  .sheet{position:absolute;top:79px;width:338px;height:438px;background:var(--white);box-shadow:0 6px 18px rgba(0,0,0,.18);overflow:hidden}
  .sheet--about{left:57px}
  .sheet--method{left:429px}
  .sheet--rules{left:802px}
  .abs{position:absolute}

  /* header */
  .brand{position:absolute;left:10px;top:6px;width:114px;text-align:center;color:var(--navy);font-weight:600}
  .brand__name{font-size:15px;letter-spacing:.5px;line-height:15px}
  .brand__tag{font-size:5.4px;letter-spacing:1.6px;margin-top:2px;display:flex;align-items:center;gap:4px;justify-content:center}
  .brand__tag::before,.brand__tag::after{content:"";width:12px;height:1px;background:var(--navy)}
  .title-bar{position:absolute;left:131px;top:0;right:0;height:29px;background:var(--navy);color:var(--white);font-family:var(--head);font-size:20px;display:flex;align-items:center;justify-content:center;letter-spacing:.3px}

  /* page 1 */
  .steps{position:absolute;left:0;top:48px;width:338px;height:60px}
  .step{position:absolute;width:56px;margin-left:-28px;text-align:center;font-size:5.8px;font-weight:600;color:var(--navy);line-height:1.2}
  .step__label{top:119px}
  .step__dots{position:absolute;left:27px;top:18px;height:36px;border-left:1.2px dotted var(--navy)}
  .step__mid{top:179px;height:20px;display:flex;align-items:center;justify-content:center}
  .step__arrow{position:absolute;top:200px;width:56px;margin-left:-28px;height:8px}
  .step__end{top:209px}
  .challenge{position:absolute;left:61px;top:233px;width:212px;height:27px;background:var(--grey);color:var(--white);font-family:var(--head);font-size:20px;display:flex;align-items:center;justify-content:center}
  .fact-col{position:absolute;top:289px;width:104px;height:139px;background:var(--panel)}
  .fact-col__head{height:29px;background:var(--navy);color:var(--white);font-weight:700;font-size:8.5px;display:flex;align-items:flex-end;justify-content:center;padding-bottom:4px;letter-spacing:.3px}
  .fact-col__badge{position:absolute;left:39px;top:-16px;width:26px;height:26px;border-radius:50%;background:var(--green);display:flex;align-items:center;justify-content:center}
  .fact-col__body{padding:5px 4px 0;font-size:4.9px;line-height:1.22;font-weight:500}
  .fact{display:flex;gap:3px;margin-bottom:2.5px}
  .fact b{font-weight:700;min-width:13px}
  .fact__src{font-style:italic;display:block}
  .fact-rule{height:.8px;background:var(--green);margin:3px 0 4px}

  /* page 2 */
  .pie{position:absolute;left:0;top:0;width:338px;height:300px}
  .pie-label{position:absolute;color:var(--white);font-weight:700;text-align:center;line-height:1.1;font-size:9.5px;letter-spacing:.3px}
  .pie-label--savings{color:var(--navy);font-size:9.5px;font-weight:800}
  .pie-label--debt{color:var(--navy)}
  .pie-label--taxes{color:var(--green)}
  .goal{position:absolute;left:265px;font-size:6.6px;font-weight:600;color:var(--navy);line-height:1.15}
  .partner{position:absolute;height:33px;width:69px;border:1px solid #c9c9c9;background:var(--white);box-shadow:0 1px 2px rgba(0,0,0,.12);display:flex;align-items:center;justify-content:center;font-weight:700;font-size:8px;color:var(--navy);gap:3px}
  .partner__dot{width:6px;height:6px;border-radius:50%;background:var(--green)}
  .pay-us{position:absolute;left:0;width:338px;top:403px;text-align:center;color:var(--green);font-weight:800;font-size:18px;letter-spacing:.5px}

  /* page 3 */
  .rate-table{position:absolute;top:43px;width:77px;height:122px;background:var(--panel)}
  .rate-table__head{height:18px;background:var(--green);color:var(--white);font-weight:700;font-size:7px;display:flex;align-items:center;padding-left:8px;position:relative}
  .rate-table__pct{position:absolute;right:2px;top:-3px;width:24px;height:24px;border-radius:50%;background:var(--navy);border:1.5px solid var(--white);color:var(--green);font-weight:700;font-size:8.5px;display:flex;align-items:center;justify-content:center}
  .rate-row{display:flex;justify-content:space-between;font-size:6.4px;font-weight:500;padding:0 6px 0 9px;height:13.2px;align-items:center}
  .rate-row b{font-weight:700}
  .rate-table__rows{padding-top:6px}
  .rate-table__base{position:absolute;left:0;right:0;bottom:-2px;height:2px;background:var(--green)}
  .rate-table__tip{position:absolute;left:34px;bottom:-6px;width:0;height:0;border-left:4px solid transparent;border-right:4px solid transparent;border-top:4px solid var(--green)}
  .rate-note{position:absolute;top:171px;width:77px;text-align:center;font-size:6px;line-height:1.3;font-weight:500;color:var(--navy)}
  .rate-note b{font-weight:700}
  .taxes-tag{position:absolute;left:0;top:202px;width:65px;height:29px;background:var(--grey);color:var(--white);font-family:var(--head);font-size:20px;display:flex;align-items:center;justify-content:center}
  .roof{position:absolute;left:0;top:200px;width:338px;height:70px}
  .pillar-head{position:absolute;top:274px;width:74px;height:15px;background:var(--navy);color:var(--white);font-weight:700;font-size:7.5px;display:flex;align-items:center;justify-content:center;clip-path:polygon(0 0,100% 0,93% 100%,7% 100%)}
  .pillar{position:absolute;top:289px;width:61px;height:90px;background:var(--panel);font-size:5.8px;font-weight:500;text-align:center;line-height:1.3;padding:5px 2px 0;color:var(--ink)}
  .pillar p{margin-bottom:6px}
  .pillar-base{position:absolute;top:379px;width:61px;height:13px;background:var(--navy);color:var(--green);font-weight:700;font-size:6.8px;display:flex;align-items:center;justify-content:center}
  .foundation{position:absolute;left:18px;top:397px;width:305px;height:31px;background:var(--green);display:grid;grid-template-columns:1fr 1fr;grid-template-rows:1fr 1fr;color:var(--white);font-weight:700;font-size:6.8px}
  .foundation span{display:flex;align-items:center;justify-content:center;letter-spacing:.3px}
  .foundation span:nth-child(odd){border-right:1px solid var(--white)}
  .foundation span:nth-child(-n+2){border-bottom:1px solid var(--white)}
</style>
</head>
<body>

<!-- Sheet 1: who we are -->
<section class="sheet sheet--about">
  <div class="brand"><div class="brand__name">KESTRELWAY</div><div class="brand__tag">FINANCIAL PLANS</div></div>
  <div class="title-bar">WHO ARE WE &amp; WHAT WE DO</div>

  <svg class="steps" viewBox="0 48 338 60" aria-hidden="true">
    <g stroke="#fff" stroke-width="2">
      <circle cx="40" cy="78" r="29" fill="#16213a"/>
      <circle cx="91" cy="78" r="29" fill="#1fae4b"/>
      <circle cx="144" cy="78" r="29" fill="#a6a8ab"/>
      <circle cx="196" cy="78" r="29" fill="#16213a"/>
      <circle cx="247" cy="78" r="29" fill="#1fae4b"/>
      <circle cx="299" cy="78" r="29" fill="#a6a8ab"/>
    </g>
    <g fill="#fff" stroke="#d6d6d6" stroke-width="1.5">
      <circle cx="40" cy="78" r="19"/><circle cx="91" cy="78" r="19"/><circle cx="144" cy="78" r="19"/>
      <circle cx="196" cy="78" r="19"/><circle cx="247" cy="78" r="19"/><circle cx="299" cy="78" r="19"/>
    </g>
    <g fill="#1fae4b">
      <rect x="30" y="72" width="20" height="12" rx="1.5"/>
      <circle cx="40" cy="78" r="3" fill="#fff"/>
      <path d="M80 78 A11 9 0 0 1 102 78 Z"/>
      <rect x="90.2" y="78" width="1.6" height="9"/>
      <rect x="133" y="71" width="22" height="14" rx="1.5"/>
      <rect x="133" y="74" width="22" height="2.5" fill="#fff"/>
      <line x1="132" y1="87" x2="156" y2="70" stroke="#fff" stroke-width="2"/>
      <rect x="185" y="71" width="16" height="13" rx="1"/>
      <path d="M201 74 h5 l3 4 v6 h-8 z"/>
      <rect x="191.5" y="73.5" width="3" height="8" fill="#fff"/>
      <rect x="189" y="76" width="8" height="3" fill="#fff"/>
      <circle cx="190" cy="85" r="2.2"/><circle cx="204" cy="85" r="2.2"/>
      <ellipse cx="247" cy="79" rx="10" ry="7.5"/>
      <rect x="241" y="84" width="3" height="4"/><rect x="250" y="84" width="3" height="4"/>
      <rect x="288" y="68" width="22" height="20" rx="1.5"/>
      <rect x="291" y="71" width="16" height="14" fill="#fff"/>
      <circle cx="299" cy="78" r="3.5" fill="#1fae4b"/>
    </g>
  </svg>

  <div class="step step__label" style="left:40px;top:123px">CASH FLOW</div>
  <div class="step step__label" style="left:91px">CASH FLOW<br>PROTECTION</div>
  <div class="step step__label" style="left:144px">DEBT<br>MANAGEMENT</div>
  <div class="step step__label" style="left:196px">EMERGENCY<br>FUND</div>
  <div class="step step__label" style="left:247px">BUILD<br>WEALTH</div>
  <div class="step step__label" style="left:299px">PRESERVE<br>WEALTH</div>

  <div class="step" style="left:40px;top:116px"><span class="step__dots"></span></div>
  <div class="step" style="left:91px;top:116px"><span class="step__dots"></span></div>
  <div class="step" style="left:144px;top:116px"><span class="step__dots"></span></div>
  <div class="step" style="left:196px;top:116px"><span class="step__dots"></span></div>
  <div class="step" style="left:247px;top:116px"><span class="step__dots"></span></div>
  <div class="step" style="left:299px;top:116px"><span class="step__dots"></span></div>

  <div class="step step__mid" style="left:40px">ANALYZE</div>
  <div class="step step__mid" style="left:91px">INCOME<br>PROTECTION</div>
  <div class="step step__mid" style="left:144px">20%</div>
  <div class="step step__mid" style="left:196px">IF / WHEN</div>
  <div class="step step__mid" style="left:247px;top:184px">FINANCIAL<br>INDEPENDENCE<br>NUMBER (FIN)</div>
  <div class="step step__mid" style="left:299px">LEAVING<br>A LEGACY</div>

  <svg class="step__arrow" style="left:40px" viewBox="0 0 56 8" aria-hidden="true"><path d="M27 0h2v4h2.5l-3.5 4-3.5-4H27z" fill="#1fae4b"/></svg>
  <svg class="step__arrow" style="left:91px" viewBox="0 0 56 8" aria-hidden="true"><path d="M27 0h2v4h2.5l-3.5 4-3.5-4H27z" fill="#1fae4b"/></svg>
  <svg class="step__arrow" style="left:144px" viewBox="0 0 56 8" aria-hidden="true"><path d="M27 0h2v4h2.5l-3.5 4-3.5-4H27z" fill="#1fae4b"/></svg>
  <svg class="step__arrow" style="left:196px" viewBox="0 0 56 8" aria-hidden="true"><path d="M27 0h2v4h2.5l-3.5 4-3.5-4H27z" fill="#1fae4b"/></svg>
  <svg class="step__arrow" style="left:299px" viewBox="0 0 56 8" aria-hidden="true"><path d="M27 0h2v4h2.5l-3.5 4-3.5-4H27z" fill="#1fae4b"/></svg>

  <div class="step step__end" style="left:40px">Free Up</div>
  <div class="step step__end" style="left:91px">Life Insurance<br>CI/DI Insurance</div>
  <div class="step step__end" style="left:144px">6-7%</div>
  <div class="step step__end" style="left:196px">3-6 Months</div>
  <div class="step step__end" style="left:299px">Will Prep</div>

  <div class="challenge">THE FINANCIAL CHALLENGE</div>

  <div class="fact-col" style="left:10px">
    <div class="fact-col__badge"><svg width="14" height="12" viewBox="0 0 14 12" aria-hidden="true"><ellipse cx="7" cy="5.5" rx="6" ry="4.5" fill="#fff"/><rect x="3" y="8" width="2" height="3" fill="#fff"/><rect x="9" y="8" width="2" height="3" fill="#fff"/></svg></div>
    <div class="fact-col__head">SAVINGS</div>
    <div class="fact-col__body">
      <div class="fact"><b>49%</b><span>of Canadian Employees are living paycheque to paycheque.</span></div>
      <div class="fact"><b>25%</b><span>Canadians are unable to cover an unexpected $500 expense. <i class="fact__src">National Stats Office (Feb 2023)</i></span></div>
      <div class="fact-rule"></div>
      <div class="fact"><b>25%</b><span>of Canadians need to access their retirement savings early.</span></div>
      <div class="fact"><b>20%</b><span>Canadians have no saving</span></div>
      <div class="fact"><b>39%</b><span>of Canadians aged 55-65 have less than $5,000 in savings. <i class="fact__src">Federal Data Office (June 2023)</i></span></div>
    </div>
  </div>

  <div class="fact-col" style="left:117px">
    <div class="fact-col__badge"><svg width="14" height="11" viewBox="0 0 14 11" aria-hidden="true"><rect x="0" y="1" width="14" height="9" rx="1" fill="#fff"/><rect x="0" y="3" width="14" height="1.6" fill="#1fae4b"/><line x1="0" y1="11" x2="14" y2="0" stroke="#1fae4b" stroke-width="1.2"/></svg></div>
    <div class="fact-col__head">DEBT</div>
    <div class="fact-col__body">
      <div class="fact"><span>The average Canadian has $22,131 in consumer debts, which excludes mortgages. <i class="fact__src">Creditline Research (Aug 2024)</i></span></div>
      <div class="fact-rule"></div>
      <div class="fact"><span>Over 55% of Canadians hold credit card debt and the total Canadian household debt has increased to $2.52 trillion, including consumer credit, mortgage and non-mortgage loans. <i class="fact__src">Bankers Forum (Aug 2024)</i></span></div>
    </div>
  </div>

  <div class="fact-col" style="left:224px">
    <div class="fact-col__badge"><svg width="14" height="13" viewBox="0 0 14 13" aria-hidden="true"><path d="M0 6 A7 6 0 0 1 14 6 Z" fill="#fff"/><rect x="6.3" y="6" width="1.4" height="6" fill="#fff"/></svg></div>
    <div class="fact-col__head">INSURANCE</div>
    <div class="fact-col__body">
      <div class="fact"><b>49%</b><span>of Canadians do not have individual life insurance coverage, but</span></div>
      <div class="fact"><b>48%</b><span>say their families would face financial trouble within 6 months of losing someone. <i class="fact__src">Lifewise Research (Apr 2023)</i></span></div>
      <div class="fact-rule"></div>
      <div class="fact"><span>2-in-5 Canadians (43% Women / 44% Men) will be diagnosed with a form of cancer or other critical illness during their lifetime. Every 7 seconds. <i class="fact__src">Health Data Portal (June 2024)</i></span></div>
    </div>
  </div>
</section>

<!-- Sheet 2: how we do it -->
<section class="sheet sheet--method">
  <div class="brand"><div class="brand__name">KESTRELWAY</div><div class="brand__tag">FINANCIAL PLANS</div></div>
  <div class="title-bar">HOW ARE WE DOING IT</div>

  <svg class="pie" viewBox="0 0 338 300" role="img" aria-label="Pie chart: living expenses, taxes, debt and savings">
    <circle cx="134" cy="151" r="105" fill="#e6e6e6"/>
    <path d="M134 151 L134 54 A97 97 0 0 0 134 248 Z" fill="#1fae4b"/>
    <path d="M134 151 L134 54 A97 97 0 0 1 231 151 Z" fill="#16213a"/>
    <path d="M134 151 L231 151 A97 97 0 0 1 134 248 Z" fill="#a6a8ab"/>
    <line x1="134" y1="54" x2="134" y2="248" stroke="#fff" stroke-width="2"/>
    <line x1="134" y1="151" x2="231" y2="151" stroke="#fff" stroke-width="3"/>
    <line x1="231" y1="151" x2="239" y2="151" stroke="#a6a8ab" stroke-width="1.2"/>
    <circle cx="134" cy="151" r="34" fill="#fff" stroke="#d2d2d2" stroke-width="4"/>
    <g stroke="#a6a8ab" stroke-width="1.2" fill="none">
      <line x1="239" y1="77" x2="239" y2="228"/>
      <line x1="239" y1="77" x2="250" y2="77"/>
      <line x1="239" y1="126" x2="250" y2="126"/>
      <line x1="239" y1="180" x2="250" y2="180"/>
      <line x1="239" y1="228" x2="250" y2="228"/>
    </g>
    <rect x="174" y="85" width="16" height="18" fill="none" stroke="#1fae4b" stroke-width="1.6"/>
    <line x1="177" y1="94" x2="187" y2="94" stroke="#1fae4b" stroke-width="1.2"/>
    <line x1="177" y1="98" x2="187" y2="98" stroke="#1fae4b" stroke-width="1.2"/>
    <rect x="171" y="177" width="20" height="13" fill="none" stroke="#16213a" stroke-width="1.6"/>
    <line x1="170" y1="192" x2="192" y2="175" stroke="#16213a" stroke-width="1.6"/>
    <rect x="77" y="130" width="22" height="13" fill="none" stroke="#fff" stroke-width="1.6"/>
    <circle cx="88" cy="136.5" r="3" fill="#fff"/>
    <ellipse cx="134" cy="138" rx="10" ry="7" fill="#1fae4b"/>
  </svg>

  <div class="pie-label" style="left:30px;top:146px;width:70px">LIVING<br>EXPENSES</div>
  <div class="pie-label pie-label--taxes" style="left:154px;top:111px;width:68px">TAXES</div>
  <div class="pie-label pie-label--savings" style="left:100px;top:153px;width:68px">SAVINGS</div>
  <div class="pie-label pie-label--debt" style="left:154px;top:196px;width:56px">DEBT</div>

  <div class="goal" style="top:70px">RETIREMENT<br>SAVINGS</div>
  <div class="goal" style="top:119px">CHILDREN'S<br>EDUCATION</div>
  <div class="goal" style="top:173px">PROPER<br>PROTECTION</div>
  <div class="goal" style="top:221px">FREEDOM<br>FROM DEBT</div>

  <div class="partner" style="left:58px;top:264px"><span class="partner__dot"></span>Harborline</div>
  <div class="partner" style="left:133px;top:264px">Cedarview Life</div>
  <div class="partner" style="left:207px;top:264px">Summit Ridge</div>
  <div class="partner" style="left:24px;top:304px"><span class="partner__dot"></span>Laurentide</div>
  <div class="partner" style="left:99px;top:304px">Alder Mutual</div>
  <div class="partner" style="left:174px;top:304px">Riverbank</div>
  <div class="partner" style="left:249px;top:304px;font-size:9.5px">Brightmoor</div>
  <div class="partner" style="left:64px;top:343px">Granite</div>
  <div class="partner" style="left:139px;top:343px;font-size:11px">Velora</div>
  <div class="partner" style="left:214px;top:343px">Fieldstone</div>

  <svg class="abs" style="left:163px;top:384px" width="12" height="14" viewBox="0 0 12 14" aria-hidden="true"><path d="M4.5 0h3v7h4L6 14 0.5 7h4z" fill="#16213a"/></svg>
  <div class="pay-us">PAY US</div>
</section>

<!-- Sheet 3: rule of 72 and taxes -->
<section class="sheet sheet--rules">
  <div class="brand"><div class="brand__name">KESTRELWAY</div><div class="brand__tag">FINANCIAL PLANS</div></div>
  <div class="title-bar">RULE OF 72</div>

  <div class="rate-table" style="left:9px">
    <div class="rate-table__head">AGE<span class="rate-table__pct">4%</span></div>
    <div class="rate-table__rows">
      <div class="rate-row"><b>29</b><span>$10,000</span></div>
      <div class="rate-row"><b>47</b><span>$20,000</span></div>
      <div class="rate-row"><b>65</b><span>$40,000</span></div>
    </div>
    <span class="rate-table__base"></span><span class="rate-table__tip"></span>
  </div>
  <div class="rate-table" style="left:90px">
    <div class="rate-table__head">AGE<span class="rate-table__pct">6%</span></div>
    <div class="rate-table__rows">
      <div class="rate-row"><b>29</b><span>$10,000</span></div>
      <div class="rate-row"><b>41</b><span>$20,000</span></div>
      <div class="rate-row"><b>53</b><span>$40,000</span></div>
      <div class="rate-row"><b>65</b><span>$80,000</span></div>
    </div>
    <span class="rate-table__base"></span><span class="rate-table__tip"></span>
  </div>
  <div class="rate-table" style="left:171px">
    <div class="rate-table__head">AGE<span class="rate-table__pct">8%</span></div>
    <div class="rate-table__rows">
      <div class="rate-row"><b>29</b><span>$10,000</span></div>
      <div class="rate-row"><b>38</b><span>$20,000</span></div>
      <div class="rate-row"><b>47</b><span>$40,000</span></div>
      <div class="rate-row"><b>56</b><span>$80,000</span></div>
      <div class="rate-row"><b>65</b><span>$160,000</span></div>
    </div>
    <span class="rate-table__base"></span><span class="rate-table__tip"></span>
  </div>
  <div class="rate-table" style="left:252px">
    <div class="rate-table__head">AGE<span class="rate-table__pct">12%</span></div>
    <div class="rate-table__rows">
      <div class="rate-row"><b>29</b><span>$10,000</span></div>
      <div class="rate-row"><b>35</b><span>$20,000</span></div>
      <div class="rate-row"><b>41</b><span>$40,000</span></div>
      <div class="rate-row"><b>47</b><span>$80,000</span></div>
      <div class="rate-row"><b>53</b><span>$160,000</span></div>
      <div class="rate-row"><b>59</b><span>$320,000</span></div>
      <div class="rate-row"><b>65</b><span>$640,000</span></div>
    </div>
    <span class="rate-table__base"></span><span class="rate-table__tip"></span>
  </div>

  <div class="rate-note" style="left:9px">Money Doubles<br><b>EVERY 18 YEARS</b></div>
  <div class="rate-note" style="left:90px">Money Doubles<br><b>EVERY 12 YEARS</b></div>
  <div class="rate-note" style="left:171px">Money Doubles<br><b>EVERY 9 YEARS</b></div>
  <div class="rate-note" style="left:252px">Money Doubles<br><b>EVERY 6 YEARS</b></div>

  <svg class="roof" viewBox="0 200 338 70" aria-hidden="true">
    <path d="M167 202 L329 262 L12 262 Z" fill="#16213a"/>
    <rect x="12" y="263" width="317" height="2" fill="#1fae4b"/>
  </svg>
  <div class="taxes-tag">TAXES</div>

  <div class="pillar-head" style="left:12px">HOME</div>
  <div class="pillar-head" style="left:92px">RRSP</div>
  <div class="pillar-head" style="left:172px">TFSA</div>
  <div class="pillar-head" style="left:253px">PERM LIFE</div>

  <div class="pillar" style="left:19px"><p>Partner with Mortgage Brokers for Best Rates</p><p>Mortgage Insurance Alternatives</p></div>
  <div class="pillar" style="left:99px"><p>Tax Deduction</p><p>Tax Deferred</p></div>
  <div class="pillar" style="left:179px"><p>No Tax Deduction</p><p>Tax Free Growth</p><p>2009 - $95,000</p><p>Limit 2023<br>$7,000/Yr</p></div>
  <div class="pillar" style="left:260px"><p>No Tax Deduction</p><p>Qualify</p><p>Tax Deferred Growth</p></div>

  <div class="pillar-base" style="left:19px">SELL</div>
  <div class="pillar-base" style="left:99px">100% TAX</div>
  <div class="pillar-base" style="left:179px">0% TAX</div>
  <div class="pillar-base" style="left:260px">0% TAX</div>

  <div class="foundation">
    <span>LIFE INSURANCE ILLNESS</span>
    <span>DEBT MANAGEMENT</span>
    <span>CRITICAL / DISABILITY</span>
    <span>CASH FLOW</span>
  </div>
</section>

</body>
</html>
```